TLV Accounting Firm Needs Graphic Art for Our Proven Processes and For Our Core Values

**Looking for redesign of attached Powerpoint content (see below)
***Final graphic should be good for web use

Date: March 10, 2017

From: Colin Ashdown, CPA
Ashdown, Pettifer & Associates, P.C. (TLV)

Background:

TLV is a 20 person Houston based CPA firm, providing tax, accounting, financial and consulting services, to individuals and to entrepreneurs and their businesses. TLV is engaged in a process called KLU (See the book Headway, by Lars Obermeyer) whereby we implement a “system” to operate our company. As part of this system we have defined what we call our “Proven Process”. This is something we will show all prospective clients, and have on our website, that explains what it looks like to work with us. Starting at the beginning of the project to completion.

Project Description:

TLV is looking for graphic artist assistance in designing the following pieces:

1. Graphic depiction of “The TLV Way”, otherwise known as our “Proven Process”. The first attachments labeled TLV will show what we have done ourselves. These will show the general steps we have defined in both a sort of graphic way and a step by step narrative. The second attachment shows you some actual examples other firms have put together, hopefully that will show you what we are asking you to develop for us. Note that we are very open to any suggested clarifications or improvements to what we have done which may include changing phrases or saying something in a different way. Remember we are accountants!

2. We have defined our core values as a company, and we are wanting to develop some posters/placards so we can post them in our conference rooms, break room, etc. Attached are our core values as well as some deeper narratives about what they mean. Also included are many of the “words” we kicked around before arriving at our core values.

3. You will also find an attachment with our logo that should be incorporated, as well. Designs SHOULD INCLUDE, but not be limited to, the colors on our logo. Our end product should reflect a strong sense of our core values.

We would like to have the project in a form that would give us the option to use any/all of the information on our website, posters, brochures, etc.

Thanks in advance for your assistance.

Target Market(s)

Entrepreneurs and their companies with revenue greater than one million; Industries such as real estate, construction, trades and professional services; all in the Greater Houston Texas area

Industry/Entity Type

Accounting

Font styles to use
Serif
Other font styles liked:
• We are okay with Serif but are open.

Requirements
Must have
• Proven Process must be presented in a way that is clear and makes sense.
Nice to have
• Clean lines
• Colors should go with logo (see attached)
Should not have
• Can't think of anything - unless I see it

```html
<!DOCTYPE html>
<html lang="en">
<head>
<meta charset="UTF-8">
<title>TLV's Core Values</title>
<link rel="stylesheet" href="https://fonts.googleapis.com/css2?family=Archivo+Black&family=Pacifico&family=Roboto+Condensed:wght@400;700;800&display=swap">
<style>
  :root {
    --forest: #1d4226;
    --gold: #c29a2e;
    --yellow: #f7d35a;
    --lavender: #9a9cc8;
    --lilac: #aaa5d6;
    --mint: #a8d8b8;
    --sage: #cfe8c4;
    --peach: #f9d6c8;
    --sky: #a8d9e2;
    --ice: #c8e6f0;
    --silver: #d2d2d2;
    --slate: #b5bec5;
    --grey: #b8b8b8;
    --olive: #5b5a22;
    --paper: #ffffff;
  }
  * { margin: 0; padding: 0; box-sizing: border-box; }
  html, body { width: 1200px; height: 900px; overflow: hidden; background: var(--paper); }
  .slide { position: relative; width: 1200px; height: 900px; overflow: hidden; background: var(--paper); }
  .slide-title {
    position: absolute; left: 61px; top: 81px;
    font-family: "Archivo Black", sans-serif; font-size: 39px; letter-spacing: 0.5px;
    color: var(--forest); line-height: 1;
  }
  .value-cloud { position: absolute; inset: 0; list-style: none; }
  .value {
    position: absolute; white-space: nowrap; line-height: 1;
    font-family: "Roboto Condensed", sans-serif; font-size: 37px; font-weight: 400;
    letter-spacing: -0.5px;
    transform: translate(-50%, -50%) rotate(var(--r, 0deg));
  }
  .value--core { color: var(--forest); font-weight: 800; font-size: 43px; }
  .value--heavy { font-weight: 700; }
  .value--round { font-family: "Archivo Black", sans-serif; letter-spacing: 0; }
  .value--script { font-family: "Pacifico", cursive; font-size: 30px; letter-spacing: 0; }

  .firm-mark {
    position: absolute; left: 60px; top: 772px;
    display: flex; align-items: center; gap: 14px;
  }
  .firm-mark__square { width: 30px; height: 30px; background: var(--gold); flex: none; }
  .firm-mark__name {
    font-family: "Roboto Condensed", sans-serif; font-size: 30px; font-weight: 400;
    color: var(--olive); line-height: 1; white-space: nowrap;
  }
</style>
</head>
<body>
<main class="slide">
  <h1 class="slide-title">TLV’S CORE VALUES</h1>

  <ul class="value-cloud">
    <li class="value" style="left:116px;top:360px;--r:65deg;color:var(--lavender)">Motivated</li>
    <li class="value" style="left:236px;top:304px;--r:-38deg;color:var(--peach)">Gets thing done</li>
    <li class="value" style="left:420px;top:260px;--r:8deg;color:var(--lavender)">Respectful</li>
    <li class="value" style="left:244px;top:368px;--r:-35deg;color:var(--mint)">Hungry</li>
    <li class="value" style="left:380px;top:336px;--r:22deg;color:var(--gold)">humor</li>
    <li class="value" style="left:452px;top:346px;--r:62deg;color:var(--lavender)">Positive</li>
    <li class="value" style="left:588px;top:284px;--r:20deg;color:var(--yellow)">Fair</li>
    <li class="value value--script" style="left:548px;top:348px;color:var(--yellow)">Great</li>
    <li class="value" style="left:748px;top:292px;--r:13deg;color:var(--sage)">Encourager</li>
    <li class="value" style="left:800px;top:252px;--r:15deg;color:var(--peach)">Honest</li>
    <li class="value" style="left:864px;top:224px;--r:62deg;color:var(--yellow)">Sense</li>
    <li class="value" style="left:944px;top:228px;--r:-58deg;color:var(--yellow)">Trust</li>
    <li class="value value--round" style="left:1006px;top:252px;--r:-20deg;font-size:22px;color:var(--sage)">Energetic Attitude</li>
    <li class="value" style="left:1052px;top:300px;--r:-38deg;color:var(--lavender)">Creative</li>
    <li class="value value--core" style="left:1092px;top:352px;--r:55deg">Fun</li>
    <li class="value value--heavy" style="left:708px;top:346px;font-size:40px;color:var(--silver)">Happy</li>
    <li class="value" style="left:744px;top:412px;--r:-78deg;color:var(--sky)">Professional</li>
    <li class="value" style="left:824px;top:374px;--r:-60deg;color:var(--silver)">achievement</li>
    <li class="value" style="left:944px;top:400px;--r:75deg;color:var(--yellow)">Competitive</li>
    <li class="value" style="left:1052px;top:412px;--r:12deg;color:var(--lilac)">Empathetic</li>
    <li class="value" style="left:864px;top:424px;--r:-15deg;color:var(--silver)">Clients</li>
    <li class="value" style="left:308px;top:410px;--r:-15deg;color:var(--lilac)">Servant</li>
    <li class="value" style="left:420px;top:416px;--r:45deg;color:var(--lavender)">Growth</li>
    <li class="value" style="left:380px;top:452px;--r:10deg;color:var(--gold)">Listens</li>
    <li class="value value--core" style="left:524px;top:446px;--r:-42deg">Value Long Term</li>
    <li class="value value--core" style="left:582px;top:472px;--r:-42deg">Relationships</li>
    <li class="value value--core" style="left:158px;top:502px;--r:33deg">Team Player</li>
    <li class="value value--heavy" style="left:266px;top:480px;font-size:34px;color:var(--gold)">excellence</li>
    <li class="value" style="left:680px;top:516px;--r:85deg;color:var(--slate)">Integrity</li>
    <li class="value" style="left:870px;top:492px;--r:10deg;color:var(--sky)">Tenacious</li>
    <li class="value value--core" style="left:1032px;top:552px;--r:78deg">Conscientious</li>
    <li class="value" style="left:1088px;top:502px;--r:35deg;color:var(--silver)">Committed</li>
    <li class="value" style="left:318px;top:534px;--r:-40deg;color:var(--sage)">Ethical</li>
    <li class="value" style="left:166px;top:586px;--r:28deg;color:var(--grey)">Accountable</li>
    <li class="value" style="left:324px;top:598px;color:var(--peach)">Deliver</li>
    <li class="value" style="left:432px;top:588px;--r:35deg;color:var(--grey)">learning</li>
    <li class="value" style="left:540px;top:572px;--r:-30deg;color:var(--lavender)">Smiles</li>
    <li class="value" style="left:622px;top:564px;--r:-70deg;color:var(--slate)">always</li>
    <li class="value" style="left:752px;top:546px;--r:50deg;color:var(--lavender)">Others</li>
    <li class="value" style="left:804px;top:524px;--r:45deg;color:var(--gold)">Works</li>
    <li class="value" style="left:942px;top:560px;--r:-60deg;color:var(--slate)">Helpful</li>
    <li class="value value--round" style="left:300px;top:650px;--r:-10deg;font-size:29px;color:var(--sage)">Valuable</li>
    <li class="value" style="left:412px;top:650px;--r:-30deg;color:var(--ice)">Well</li>
    <li class="value" style="left:532px;top:632px;--r:-32deg;color:var(--yellow)">Winner</li>
    <li class="value value--heavy" style="left:680px;top:620px;font-size:30px;color:#a0a0a0">minded</li>
    <li class="value" style="left:620px;top:660px;--r:-5deg;color:var(--yellow)">right</li>
    <li class="value value--core" style="left:754px;top:660px;--r:-20deg">Caring</li>
    <li class="value" style="left:856px;top:612px;--r:18deg;color:var(--yellow)">Always</li>
    <li class="value" style="left:972px;top:640px;--r:-15deg;color:var(--gold)">Strives</li>
  </ul>

  <footer class="firm-mark">
    <span class="firm-mark__square"></span>
    <span class="firm-mark__name">Ashdown, Pettifer &amp; Associates, PC</span>
  </footer>
</main>
</body>
</html>
```